Quellfield Air Business Card Design

Design new, 2 sides, business cards for a residential and light commercial heating, air conditioning contractor.

Target Market(s)

Homeowners, small businesses

Industry/Entity Type

Business

Contact Information for Business Card

Dominic Westerhall
Phone - 862-415-2736
Email
Address - PO box 518
Brightwater NJ 07912
Website - www.HarborBreezeLLC.example

Requirements
Must have
• logo, company colors, standard size with no die cut, so I can use nova stamp

```html
<!DOCTYPE html>
<html lang="en">
<head>
<meta charset="utf-8">
<title>Quellfield Air Business Card</title>
<link href="https://fonts.googleapis.com/css2?family=Raleway:wght@500;700;800&display=swap" rel="stylesheet">
<style>
  :root {
    --maroon: #9b2238;
    --orange: #f39a1e;
    --white: #ffffff;
    --stage: #ece8e2;
  }
  * { box-sizing: border-box; margin: 0; padding: 0; }
  html, body { width: 1200px; height: 950px; overflow: hidden; }
  body {
    background: var(--stage);
    font-family: "Raleway", Arial, sans-serif;
    position: relative;
  }
  .card {
    position: absolute;
    top: 107px;
    width: 420px;
    height: 735px;
    overflow: hidden;
    box-shadow: 0 6px 18px rgba(0,0,0,0.18);
  }
  .card-front { left: 150px; background: var(--white); }
  .card-back { left: 630px; background: var(--orange); }

  .front-shape { position: absolute; inset: 0; width: 100%; height: 100%; }

  .brand {
    position: absolute;
    left: 0; right: 0;
    display: flex;
    align-items: center;
    justify-content: center;
    gap: 12px;
  }
  .brand-front { top: 165px; }
  .brand-back { top: 0; bottom: 0; }
  .brand-dot {
    width: 22px; height: 22px;
    border-radius: 50%;
    background: var(--orange);
    flex: none;
  }
  .brand-back .brand-dot { background: var(--maroon); }
  .brand-name {
    font-weight: 800;
    font-size: 36px;
    letter-spacing: 0.5px;
    color: var(--maroon);
    text-transform: uppercase;
    white-space: nowrap;
  }

  .contact {
    position: absolute;
    right: 36px;
    top: 480px;
    text-align: right;
    color: var(--white);
  }
  .contact-name {
    font-weight: 700;
    font-size: 22px;
    color: var(--orange);
    text-transform: uppercase;
    letter-spacing: 0.5px;
  }
  .contact-title {
    font-weight: 500;
    font-size: 16px;
    text-transform: uppercase;
    margin-bottom: 18px;
  }
  .contact-address {
    font-size: 15px;
    line-height: 1.35;
    margin-bottom: 16px;
  }
  .contact-list { list-style: none; font-size: 15px; }
  .contact-list li {
    display: flex;
    justify-content: flex-end;
    align-items: center;
    gap: 10px;
    line-height: 21px;
  }
  .contact-icon { width: 14px; height: 14px; flex: none; }
</style>
</head>
<body>

<section class="card card-front" aria-label="Business card front">
  <svg class="front-shape" viewBox="0 0 420 735" preserveAspectRatio="none" aria-hidden="true">
    <path d="M0 455 C140 380 290 415 420 355 L420 735 L0 735 Z" fill="var(--orange)"/>
    <path d="M0 472 C150 395 300 435 420 378 L420 735 L0 735 Z" fill="var(--maroon)"/>
  </svg>

  <div class="brand brand-front">
    <span class="brand-dot"></span>
    <span class="brand-name">Quellfield Air</span>
  </div>

  <div class="contact">
    <p class="contact-name">Dominic Westerhall</p>
    <p class="contact-title">President</p>
    <p class="contact-address">PO box 518<br>Brightwater NJ 07912</p>
    <ul class="contact-list">
      <li>862-415-2736
        <svg class="contact-icon" viewBox="0 0 16 16"><path d="M4 1l3 3-2 2c1 2 3 4 5 5l2-2 3 3-2 3C7 15 1 9 1 3z" fill="var(--orange)"/></svg>
      </li>
      <li>862-415-2740
        <svg class="contact-icon" viewBox="0 0 16 16"><rect x="4" y="1" width="8" height="14" rx="1.5" fill="var(--orange)"/><rect x="5.5" y="3" width="5" height="8" fill="var(--maroon)"/></svg>
      </li>
      <li>862-415-2741
        <svg class="contact-icon" viewBox="0 0 16 16"><rect x="4" y="1" width="8" height="5" fill="var(--orange)"/><rect x="1" y="6" width="14" height="7" rx="1" fill="var(--orange)"/><rect x="4" y="10" width="8" height="5" fill="var(--white)"/></svg>
      </li>
      <li>dominic@quellfieldair.example
        <svg class="contact-icon" viewBox="0 0 16 16"><rect x="1" y="3" width="14" height="10" rx="1" fill="var(--orange)"/><path d="M1 4l7 5 7-5" fill="none" stroke="var(--maroon)" stroke-width="1.3"/></svg>
      </li>
      <li>www.QuellfieldAirLLC.example
        <svg class="contact-icon" viewBox="0 0 16 16"><circle cx="8" cy="8" r="7" fill="var(--orange)"/><path d="M1 8h14M8 1c-3 4-3 10 0 14M8 1c3 4 3 10 0 14" fill="none" stroke="var(--maroon)" stroke-width="1"/></svg>
      </li>
    </ul>
  </div>
</section>

<section class="card card-back" aria-label="Business card back">
  <div class="brand brand-back">
    <span class="brand-dot"></span>
    <span class="brand-name">Quellfield Air</span>
  </div>
</section>

</body>
</html>
```